Im open to ideas.. I was thinking on my business cards aswell as my logo. a place for my name. email. phone number and abn..

ive attched a file with my business logo. which i dont love the colours.. i was think a dark background with charcoal letters so something along those colour schumes but im open to ideas..

BRM Constructions

```html
<!DOCTYPE html>
<html lang="en">
<head>
<meta charset="utf-8">
<title>BRM Constructions – Business Cards</title>
<link rel="stylesheet" href="https://fonts.googleapis.com/css2?family=Arimo:wght@400;700&display=swap">
<style>
  :root {
    --page-bg: #d9d6d2;
    --card-black: #161616;
    --card-edge: #0c0c0c;
    --text-white: #f2f2f2;
    --text-grey: #cfcfcf;
    --muted-grey: #5d5d5d;
    --accent-red: #e0141b;
    --divider: #6a6a6a;
  }
  * { margin: 0; padding: 0; box-sizing: border-box; }
  html, body {
    width: 1200px;
    height: 787px;
    overflow: hidden;
    background: var(--page-bg);
    font-family: "Arimo", Arial, sans-serif;
  }
  .sheet {
    position: relative;
    width: 1200px;
    height: 787px;
  }
  .card {
    position: absolute;
    top: 239px;
    width: 540px;
    height: 309px;
    background: var(--card-black);
    border: 1px solid var(--card-edge);
    box-shadow: 0 10px 24px rgba(0,0,0,0.25);
  }
  .card--back { left: 40px; }
  .card--front { left: 620px; }

  /* back */
  .back-name {
    position: absolute;
    left: 0; right: 0;
    top: 112px;
    text-align: center;
    font-weight: 700;
    font-size: 30px;
    letter-spacing: 3px;
    color: var(--muted-grey);
    text-transform: uppercase;
  }
  .back-url {
    position: absolute;
    left: 0; right: 0;
    bottom: 52px;
    text-align: center;
    font-size: 14px;
    letter-spacing: 6px;
    color: var(--text-grey);
  }

  /* front */
  .brand {
    position: absolute;
    left: 34px;
    top: 0;
    width: 250px;
    height: 309px;
    display: flex;
    flex-direction: column;
    justify-content: center;
    align-items: center;
  }
  .brand-name {
    font-weight: 700;
    font-size: 40px;
    line-height: 1;
    color: var(--text-white);
    letter-spacing: 2px;
    text-transform: uppercase;
    text-align: center;
  }
  .brand-name span {
    display: block;
    font-size: 14px;
    letter-spacing: 7px;
    margin-top: 8px;
  }
  .divider {
    position: absolute;
    left: 300px;
    top: 70px;
    width: 1px;
    height: 170px;
    background: var(--divider);
  }
  .details {
    position: absolute;
    left: 322px;
    top: 78px;
    color: var(--text-grey);
    font-size: 15px;
  }
  .person-name {
    font-size: 19px;
    color: var(--accent-red);
    line-height: 1.1;
  }
  .person-title {
    font-size: 16px;
    color: var(--text-white);
    margin-bottom: 12px;
  }
  .abn { margin-bottom: 12px; }
  .contact-line {
    display: flex;
    align-items: center;
    gap: 10px;
    margin-bottom: 8px;
  }
  .contact-line svg { width: 15px; height: 13px; flex: none; }
</style>
</head>
<body>
<main class="sheet">
  <section class="card card--back" aria-label="Card back">
    <div class="back-name">BRM Constructions</div>
    <div class="back-url">www.brmbuild.com</div>
  </section>

  <section class="card card--front" aria-label="Card front">
    <div class="brand">
      <div class="brand-name">BRM<span>Constructions</span></div>
    </div>
    <div class="divider"></div>
    <div class="details">
      <div class="person-name">Daniel Marsh</div>
      <div class="person-title">President</div>
      <div class="abn">ABN: 987654321</div>
      <div class="contact-line">
        <svg viewBox="0 0 15 13" aria-hidden="true">
          <path fill="#e0141b" d="M1 4.5C1 2 4 1 7.5 1S14 2 14 4.5v1h-3V4H4v1.5H1z"/>
          <rect fill="#e0141b" x="2.5" y="6.5" width="10" height="6" rx="1"/>
        </svg>
        <span>555 0142 7788</span>
      </div>
      <div class="contact-line">
        <svg viewBox="0 0 15 13" aria-hidden="true">
          <rect fill="#e0141b" x="0.5" y="2" width="14" height="10" rx="1"/>
          <path d="M1 2.5l6.5 5 6.5-5" stroke="#161616" stroke-width="1.3" fill="none"/>
        </svg>
        <span>daniel@brmbuild.com</span>
      </div>
    </div>
  </section>
</main>
</body>
</html>
```